Business card design Needed for new logo / Construction business, home extensions and new builds

We need a business card design using our new logo files which i will attach to this project :)

We are a small construction business specialising in home extensions, new builds and property development. We are very ambitious and would appreciate professional and elegant designs for our new business card.

Very serious about using the services on MakerQuarry and recently acquired our new logo from here :)

Please get involved, i will feedback when i can as i am very busy but can respond daily, thanks

Target Market(s)

People that want to build onto their houses, new building developments or adding too their existing property

Industry/Entity Type

Construction

Contact Information for Business Card

Renwick Tolliver Construction, Lionel Ashby (Managing Director), Tel 07822254961, email - info@renwick-tolliver, www.renwick-tolliver.co.uk

Colors

Designer to choose colors to be used in the design.

Requirements
Must have
• I like a deep grey on the back please. A lot of you have provided black from and back, try mixing things up a little. The black looks cool 😎 Thanks

```html
<!DOCTYPE html>
<html lang="en">
<head>
<meta charset="utf-8">
<title>Renwick Tolliver Construction – Business Card</title>
<link rel="stylesheet" href="https://fonts.googleapis.com/css2?family=Cinzel:wght@600&family=Poppins:wght@400;500&display=swap">
<style>
  :root {
    --backdrop: #161616;
    --card-black: #030303;
    --card-deep-grey: #2e2e30;
    --gold-dark: #a8730f;
    --gold-mid: #d9a845;
    --gold-light: #f6d687;
    --silver-dark: #8a8a8a;
    --silver-light: #f2f2f2;
    --ink: #111111;
  }
  * { margin: 0; padding: 0; box-sizing: border-box; }
  html, body {
    width: 1200px; height: 1015px; overflow: hidden;
    background: var(--backdrop);
  }
  .canvas { position: relative; width: 1200px; height: 1015px; }

  .card {
    position: absolute; width: 640px; height: 366px;
    overflow: hidden;
    box-shadow: 0 14px 30px rgba(0,0,0,0.6);
  }
  .card--front { left: 110px; top: 100px; background: var(--card-black); }
  .card--back  { left: 450px; top: 540px; background: var(--card-deep-grey); }

  .brand {
    font-family: "Cinzel", serif; font-weight: 600;
    color: var(--gold-mid);
    text-transform: uppercase;
    display: flex; align-items: center; gap: 14px;
  }
  .brand__mark { width: 14px; height: 14px; background: var(--gold-mid); flex: none; }
  .brand__name { line-height: 1.15; letter-spacing: 1px; }

  .card--front .brand {
    position: absolute; left: 0; right: 0; top: 0; bottom: 0;
    flex-direction: column; justify-content: center;
    font-size: 30px; text-align: center; gap: 18px;
  }
  .card--front .brand__mark { width: 22px; height: 22px; }

  .card--back .brand {
    position: absolute; left: 170px; top: 70px; font-size: 22px;
  }

  .divider-line {
    position: absolute; left: 0; right: 0; top: 210px; height: 5px;
    background: linear-gradient(90deg, var(--silver-dark), var(--silver-light) 50%, var(--silver-dark));
  }
  .gold-band {
    position: absolute; left: 0; right: 0; top: 215px; bottom: 0;
    background: linear-gradient(100deg, var(--gold-dark) 0%, var(--gold-light) 48%, var(--gold-mid) 75%, var(--gold-dark) 100%);
    color: var(--ink);
  }

  .person { position: absolute; left: 42px; top: 26px; text-align: right; width: 220px; }
  .person__name { font-family: "Cinzel", serif; font-weight: 600; font-size: 21px; letter-spacing: 0.5px; white-space: nowrap; }
  .person__role { font-family: "Poppins", sans-serif; font-size: 11px; letter-spacing: 0.5px; text-transform: uppercase; }

  .split { position: absolute; left: 282px; top: 18px; width: 1px; height: 66px; background: var(--ink); }

  .contacts {
    position: absolute; left: 300px; top: 14px; list-style: none;
    font-family: "Poppins", sans-serif; font-size: 14px; line-height: 24px;
  }
  .contacts li { display: flex; align-items: center; gap: 8px; white-space: nowrap; }
  .contacts svg { width: 13px; height: 13px; flex: none; }

  .address {
    position: absolute; left: 0; right: 0; top: 106px; text-align: center;
    font-family: "Poppins", sans-serif; font-size: 14px;
  }
</style>
</head>
<body>
<main class="canvas">

  <section class="card card--front" aria-label="Business card front">
    <div class="brand">
      <span class="brand__mark"></span>
      <span class="brand__name">Renwick Tolliver<br>Construction</span>
    </div>
  </section>

  <section class="card card--back" aria-label="Business card back">
    <div class="brand">
      <span class="brand__mark"></span>
      <span class="brand__name">Renwick Tolliver<br>Construction</span>
    </div>

    <div class="divider-line"></div>

    <div class="gold-band">
      <div class="person">
        <p class="person__name">Lionel Ashby</p>
        <p class="person__role">Managing Director</p>
      </div>
      <div class="split"></div>
      <ul class="contacts">
        <li>
          <svg viewBox="0 0 24 24"><path fill="#111" d="M6.6 10.8a15 15 0 0 0 6.6 6.6l2.2-2.2a1 1 0 0 1 1-.25 11.4 11.4 0 0 0 3.6.57 1 1 0 0 1 1 1V20a1 1 0 0 1-1 1A17 17 0 0 1 3 4a1 1 0 0 1 1-1h3.5a1 1 0 0 1 1 1c0 1.25.2 2.45.57 3.57a1 1 0 0 1-.25 1z"/></svg>
          07822254961
        </li>
        <li>
          <svg viewBox="0 0 24 24"><path fill="#111" d="M2 5h20v14H2z"/><path fill="none" stroke="#e0b460" stroke-width="1.8" d="M2 5l10 8 10-8"/></svg>
          info@renwick-tolliver
        </li>
        <li>
          <svg viewBox="0 0 24 24" fill="none" stroke="#111" stroke-width="2"><circle cx="12" cy="12" r="10"/><path d="M2 12h20M12 2c3 3 3 17 0 20M12 2c-3 3-3 17 0 20"/></svg>
          www.renwick-tolliver.co.uk
        </li>
      </ul>
      <p class="address">12 Foundry Lane, Leeds LS1 4AB, United Kingdom</p>
    </div>
  </section>

</main>
</body>
</html>
```